Birchline Septic Solutions

Would like to see some single sided ones but would also like to see some double sided with one sided only being the logo. Owners name is Colin Vandro. Phone number is 555-214-0387
Services are pumping, inspections, installs, and repairs

Contact Information for Business Card

555-241-0387 Colin Vandro Maplecrest, OH

```html
<!DOCTYPE html>
<html lang="en">
<head>
<meta charset="utf-8">
<title>Birchline Septic Solutions – Business Cards</title>
<link rel="stylesheet" href="https://fonts.googleapis.com/css2?family=Montserrat:wght@400;500;700;800&display=swap">
<style>
  :root {
    --ink: #0a0a0a;
    --paper: #ffffff;
    --teal: #2bbdb3;
    --stage: #e6e6e6;
    --muted: #2a2a2a;
  }
  * { box-sizing: border-box; margin: 0; padding: 0; }
  html, body { width: 1200px; height: 880px; overflow: hidden; }
  body {
    background: var(--stage);
    font-family: "Montserrat", sans-serif;
    position: relative;
  }
  .card {
    position: absolute;
    width: 540px;
    height: 308px;
    border-radius: 4px;
    overflow: hidden;
    box-shadow: 0 10px 28px rgba(0,0,0,0.18);
  }

  /* Logo side */
  .card--logo {
    left: 70px; top: 90px;
    background: var(--ink);
    color: var(--paper);
    display: flex; flex-direction: column; align-items: center; justify-content: center;
    gap: 30px;
  }
  .wordmark {
    display: flex; align-items: center; gap: 12px;
    font-weight: 800; letter-spacing: 0.04em; text-transform: uppercase;
  }
  .wordmark__dot {
    width: 14px; height: 14px; border-radius: 50%; background: var(--teal); flex: none;
  }
  .card--logo .wordmark { font-size: 24px; color: var(--paper); }
  .services {
    font-size: 17px; font-weight: 500; line-height: 1.45; text-align: center;
  }
  .services .tick { width: 15px; height: 15px; vertical-align: -2px; margin: 0 4px; }

  /* Contact side */
  .card--contact {
    left: 590px; top: 470px;
    background: var(--paper);
    color: var(--ink);
  }
  .card--contact .wave {
    position: absolute; left: 0; bottom: 0; width: 100%; height: 118px;
  }
  .card--contact .wordmark {
    position: absolute; left: 34px; top: 84px;
    width: 226px;
    font-size: 20px; line-height: 1.2; color: var(--ink);
  }
  .card--contact .wordmark__text { display: block; }
  .divider {
    position: absolute; left: 278px; top: 56px; width: 2px; height: 110px; background: var(--teal);
  }
  .contact {
    position: absolute; left: 298px; top: 48px; width: 230px;
  }
  .contact__name { font-size: 23px; font-weight: 800; text-transform: uppercase; line-height: 1.1; white-space: nowrap; }
  .contact__name .surname { color: var(--teal); }
  .contact__role { font-size: 14px; font-weight: 500; color: var(--muted); margin: 2px 0 12px; }
  .contact__line { display: flex; align-items: center; gap: 8px; font-size: 14px; font-weight: 500; margin-top: 6px; white-space: nowrap; }
  .contact__line svg { width: 15px; height: 15px; flex: none; }
</style>
</head>
<body>

<section class="card card--logo">
  <div class="wordmark"><span class="wordmark__dot"></span>Birchline Septic Solutions</div>
  <p class="services">
    <svg class="tick" viewBox="0 0 16 16"><circle cx="8" cy="8" r="6.5" fill="none" stroke="#fff" stroke-width="1.6"/><path d="M5 8.2l2 2 4-4.2" fill="none" stroke="#fff" stroke-width="1.6"/></svg>Services are pumping<br>
    <svg class="tick" viewBox="0 0 16 16"><circle cx="8" cy="8" r="6.5" fill="none" stroke="#fff" stroke-width="1.6"/><path d="M5 8.2l2 2 4-4.2" fill="none" stroke="#fff" stroke-width="1.6"/></svg>inspections
    <svg class="tick" viewBox="0 0 16 16"><circle cx="8" cy="8" r="6.5" fill="none" stroke="#fff" stroke-width="1.6"/><path d="M5 8.2l2 2 4-4.2" fill="none" stroke="#fff" stroke-width="1.6"/></svg>installs
    <svg class="tick" viewBox="0 0 16 16"><circle cx="8" cy="8" r="6.5" fill="none" stroke="#fff" stroke-width="1.6"/><path d="M5 8.2l2 2 4-4.2" fill="none" stroke="#fff" stroke-width="1.6"/></svg>and repairs
  </p>
</section>

<section class="card card--contact">
  <svg class="wave" viewBox="0 0 540 118" preserveAspectRatio="none">
    <path d="M0 118 L0 108 C140 94 220 72 300 46 C390 18 470 8 540 4 L540 118 Z" fill="var(--ink)"/>
    <path d="M0 101 C140 87 220 65 300 39 C390 11 470 1 540 -3" fill="none" stroke="var(--teal)" stroke-width="5"/>
  </svg>

  <div class="wordmark">
    <span class="wordmark__dot"></span>
    <span class="wordmark__text">Birchline Septic Solutions</span>
  </div>
  <div class="divider"></div>

  <div class="contact">
    <h1 class="contact__name">Colin <span class="surname">Vandro</span></h1>
    <p class="contact__role">Owners</p>
    <p class="contact__line">
      <svg viewBox="0 0 16 16"><path d="M3 2h3l1.5 3.5-2 1.2a8 8 0 0 0 3.8 3.8l1.2-2L14 10v3a1 1 0 0 1-1 1A11 11 0 0 1 2 3a1 1 0 0 1 1-1z" fill="var(--teal)"/></svg>
      555-214-0387
    </p>
    <p class="contact__line">
      <svg viewBox="0 0 16 16"><path d="M8 1a5 5 0 0 0-5 5c0 3.8 5 9 5 9s5-5.2 5-9a5 5 0 0 0-5-5zm0 7a2 2 0 1 1 0-4 2 2 0 0 1 0 4z" fill="var(--teal)"/></svg>
      Colin Vandro Maplecrest, OH
    </p>
  </div>
</section>

</body>
</html>
```